Hello my Name is Elias Moreno. I buy and sell vintage comic books, you can refer to my instragram page qpkz.comics to get ideas and inspiration. For the front of the card I would like my company logo QPKZ Comics with a yellow and black background with the bat signal or bat emblem like on my IG page and with my info Elias Moreno as the Owner and address/ phone number, PO Box 617283, Miami, FL 33827, 305-482-6170 and that I buy and sell comics & collectables . Also feel free to be open to other ideas if you want. Im not stuck on one design. For the back of the card I would like for it to say follow me on Instagram QPKZ.Comics with the ig emblem. Also would like the card to be vertical if possible. Thanks

```html
<!DOCTYPE html>
<html lang="en">
<head>
<meta charset="utf-8">
<title>QPKZ Comics – Business Card</title>
<link rel="stylesheet" href="https://fonts.googleapis.com/css2?family=Open+Sans:wght@400;600;700&display=swap">
<style>
  :root {
    --yellow: #fcc915;
    --black: #111111;
    --charcoal: #1c1c1c;
    --white: #ffffff;
    --backdrop: #ecebe9;
  }
  * { box-sizing: border-box; margin: 0; padding: 0; }
  html, body { width: 1200px; height: 900px; overflow: hidden; }
  body {
    position: relative;
    background: var(--backdrop);
    font-family: "Open Sans", sans-serif;
  }
  .card {
    position: absolute;
    width: 556px;
    height: 342px;
    box-shadow: 0 4px 14px rgba(0,0,0,0.18);
  }

  /* Front */
  .card-front { left: 355px; top: 38px; background: var(--yellow); color: var(--black); }
  .brand {
    position: absolute; left: 32px; top: 104px;
    display: flex; align-items: center; gap: 12px;
  }
  .brand-dot { width: 56px; height: 56px; border-radius: 50%; background: var(--black); }
  .brand-name { font-weight: 700; font-size: 26px; color: var(--black); }
  .divider {
    position: absolute; left: 0; top: 221px; width: 357px; height: 2px; background: var(--black);
  }
  .owner-name {
    position: absolute; right: 31px; top: 209px;
    font-weight: 700; font-size: 21px; letter-spacing: 0.3px;
  }
  .owner-role {
    position: absolute; right: 31px; top: 237px;
    font-size: 16px; letter-spacing: 0.3px;
  }
  .address {
    position: absolute; left: 31px; top: 271px;
    font-size: 14.5px; line-height: 20px;
  }
  .phone {
    position: absolute; right: 24px; top: 291px;
    display: flex; align-items: center; gap: 8px; font-size: 15px;
  }
  .phone svg { width: 12px; height: 12px; }
  .footer-bar {
    position: absolute; bottom: 0; height: 9px; background: var(--black);
  }
  .footer-bar.left { left: 0; width: 272px; }
  .footer-bar.right { left: 284px; right: 0; }

  /* Back */
  .card-back {
    left: 420px; top: 510px; width: 558px;
    background: var(--yellow);
  }
  .back-panel {
    position: absolute; left: 0; right: 0; top: 10px; bottom: 9px;
    background: linear-gradient(180deg, #1e1e1e, var(--charcoal));
    color: var(--white);
  }
  .back-brand {
    position: absolute; left: 0; right: 0; top: 92px;
    display: flex; justify-content: center; align-items: center; gap: 12px;
  }
  .back-brand .brand-dot { background: var(--white); }
  .back-brand .brand-name { color: var(--white); }
  .tagline {
    position: absolute; left: 0; right: 0; top: 232px; text-align: center;
    font-weight: 700; font-size: 14.5px; letter-spacing: 0.2px;
  }
  .tagline .amp { color: var(--yellow); }
  .follow {
    position: absolute; left: 0; right: 0; top: 279px;
    display: flex; justify-content: center; align-items: center; gap: 8px;
    font-size: 14.5px;
  }
  .follow-square { width: 20px; height: 20px; border-radius: 4px; background: var(--yellow); }
</style>
</head>
<body>
  <section class="card card-front">
    <div class="brand">
      <span class="brand-dot"></span>
      <span class="brand-name">QPKZ Comics</span>
    </div>
    <div class="divider"></div>
    <p class="owner-name">ELIAS MORENO</p>
    <p class="owner-role">OWNER</p>
    <p class="address">PO Box 617283,<br>Miami, FL 33827</p>
    <p class="phone">305-482-6170
      <svg viewBox="0 0 24 24" aria-hidden="true"><path fill="currentColor" d="M6.6 10.8c1.4 2.8 3.8 5.1 6.6 6.6l2.2-2.2c.3-.3.7-.4 1-.2 1.1.4 2.3.6 3.6.6.6 0 1 .4 1 1V20c0 .6-.4 1-1 1C10.6 21 3 13.4 3 4c0-.6.4-1 1-1h3.5c.6 0 1 .4 1 1 0 1.3.2 2.5.6 3.6.1.3 0 .7-.2 1z"/></svg>
    </p>
    <div class="footer-bar left"></div>
    <div class="footer-bar right"></div>
  </section>

  <section class="card card-back">
    <div class="back-panel">
      <div class="back-brand">
        <span class="brand-dot"></span>
        <span class="brand-name">QPKZ Comics</span>
      </div>
      <p class="tagline">WE BUY AND SELL COMICS <span class="amp">&amp;</span> COLLECTABLES</p>
      <p class="follow">Follow me on <span class="follow-square"></span> QPKZ.Comics</p>
    </div>
  </section>
</body>
</html>
```